Master Label Design for Velmora Botanic Products

Looking to update product labels and add consistency across our line with a new master label design. 'Velmora Botanic' has been a trusted name in the health marketplace providing quality herbal and dietary supplements since 1979. We have 8 products in need of a master label design, examples of our current labels are attached, and you can see more at our website, VelmoraBotanic.com. All 8 products currently have a 160mm x 58mm label size, while 3 products also have a 194mm x 68mm (Chaparral, Garlic Bright, and Bulvana Odorless Garlic).
Also, our logo is only prominent on the EDTA label, but that product is our #1 seller and most recognizable, it is at the artist's discretion what to do with our logo. (attached, if needed).
Please show me only the label designs for "EDTA".
Target Market(s)
-Health-conscious adults over 40 in North America who buy herbal and/or dietary supplements.
-->Cardiovascular health-conscious adults (a.k.a., "heart healthy" adults)
-->Adults with poor cardiovascular health seeking naturopathic/alternative options.
Industry/Entity Type
Health And Wellness
Logo Text
Velmora Botanic
Colors
Designer to choose colors to be used in the design.

```html
<!DOCTYPE html>
<html lang="en">
<head>
<meta charset="UTF-8">
<title>Velmora Botanic – EDTA Label</title>
<link rel="stylesheet" href="https://fonts.googleapis.com/css2?family=Montserrat:wght@300;400;600;700&display=swap">
<style>
  :root {
    --backdrop: #a4a4a4;
    --label-teal: #1b6c6e;
    --label-teal-deep: #0f4f52;
    --art-light: #5fa8a6;
    --art-mid: #2f8583;
    --art-dark: #164f52;
    --gold: #c9a24a;
    --gold-light: #e8cf86;
    --text-white: #ffffff;
    --text-soft: #e6f1f0;
  }
  * { margin: 0; padding: 0; box-sizing: border-box; }
  html, body {
    width: 1200px;
    height: 825px;
    overflow: hidden;
  }
  body {
    background: var(--backdrop);
    font-family: "Montserrat", Arial, sans-serif;
    display: flex;
    align-items: center;
    justify-content: center;
  }
  .label {
    position: relative;
    width: 1100px;
    height: 680px;
    background: linear-gradient(90deg, var(--label-teal-deep) 0%, var(--label-teal) 30%, var(--label-teal) 70%, var(--label-teal-deep) 100%);
    display: flex;
    align-items: center;
    justify-content: center;
  }
  .front-panel {
    position: relative;
    width: 500px;
    height: 570px;
    border: 3px solid var(--gold);
    box-shadow: inset 0 0 0 1px var(--gold-light);
    overflow: hidden;
  }
  .botanical-art {
    position: absolute;
    inset: 0;
    background:
      radial-gradient(ellipse at 30% 25%, var(--art-light) 0%, transparent 55%),
      radial-gradient(ellipse at 75% 70%, var(--art-light) 0%, transparent 50%),
      linear-gradient(160deg, var(--art-mid) 0%, var(--art-dark) 100%);
    opacity: 0.9;
  }
  .panel-content {
    position: absolute;
    inset: 0;
    color: var(--text-white);
  }
  .brand-line {
    position: absolute;
    top: 34px;
    left: 0;
    right: 0;
    text-align: center;
    font-weight: 600;
    font-size: 13px;
    letter-spacing: 0.55em;
    text-transform: uppercase;
    padding-left: 0.55em;
  }
  .brand-mark {
    position: absolute;
    top: 150px;
    left: 0;
    right: 0;
    display: flex;
    align-items: center;
    justify-content: center;
    gap: 10px;
    font-weight: 600;
    font-size: 22px;
    letter-spacing: 0.08em;
    color: var(--gold-light);
  }
  .brand-mark .dot {
    width: 12px;
    height: 12px;
    border-radius: 50%;
    background: var(--gold);
  }
  .product-name {
    position: absolute;
    top: 330px;
    left: 0;
    right: 0;
    font-weight: 300;
    font-size: 44px;
    line-height: 1.15;
    text-align: center;
    text-transform: uppercase;
    letter-spacing: 0.01em;
  }
  .divider {
    position: absolute;
    top: 462px;
    left: 36px;
    right: 36px;
    height: 1.5px;
    background: var(--text-soft);
  }
  .product-meta {
    position: absolute;
    top: 480px;
    left: 36px;
    right: 36px;
    display: flex;
    justify-content: space-between;
    align-items: center;
  }
  .claims {
    font-size: 11.5px;
    font-weight: 400;
    line-height: 1.35;
    text-transform: uppercase;
    letter-spacing: 0.03em;
    color: var(--text-soft);
  }
  .count {
    display: flex;
    align-items: baseline;
    gap: 8px;
    margin-right: 8px;
  }
  .count-number {
    font-weight: 700;
    font-size: 32px;
  }
  .count-unit {
    font-weight: 400;
    font-size: 13px;
    letter-spacing: 0.04em;
    text-transform: uppercase;
  }
</style>
</head>
<body>
  <section class="label">
    <div class="front-panel">
      <div class="botanical-art" role="img" aria-label="Teal-toned botanical illustration of leaves and flowers"></div>
      <div class="panel-content">
        <p class="brand-line">Velmora Botanic</p>
        <div class="brand-mark">
          <span class="dot"></span>
          <span>Velmora Botanic</span>
        </div>
        <h1 class="product-name">EDTA<br>Chelation</h1>
        <div class="divider"></div>
        <div class="product-meta">
          <p class="claims">Heart Healthy<br>Circulation Support</p>
          <p class="count"><span class="count-number">90</span><span class="count-unit">Capsules</span></p>
        </div>
      </div>
    </div>
  </section>
</body>
</html>
```